Business card for a new cabinet shop company named Veloran Cabinets for high end cabinets

Design a business card, thinking dark rich green with colours to speak of high end luxury ie; cream, gold, black possibly

Mitchell Tarrowby
Director Craftsman
Email: info@veloranjoinery-example.com.au
Instagram : @veloran.cabinets

```html
<!DOCTYPE html>
<html lang="en">
<head>
<meta charset="utf-8">
<title>Veloran Cabinets — Business Card</title>
<link rel="stylesheet" href="https://fonts.googleapis.com/css2?family=Montserrat:wght@300;400;500;700&display=swap">
<style>
  :root {
    --backdrop: #1a1a1a;
    --card-black: #121212;
    --card-black-soft: #202020;
    --card-green: #619a42;
    --card-green-light: #6aa64a;
    --gold: #c9a46a;
    --white: #ffffff;
  }
  * { box-sizing: border-box; margin: 0; padding: 0; }
  html, body {
    width: 1200px; height: 875px; overflow: hidden;
    background: var(--backdrop);
    font-family: "Montserrat", sans-serif;
  }
  .stage {
    position: relative; width: 1200px; height: 875px;
    display: flex; align-items: center; justify-content: center; gap: 40px;
  }
  .card {
    position: relative; width: 540px; height: 315px;
    border-radius: 18px; overflow: hidden;
    box-shadow: 0 18px 40px rgba(0,0,0,.55);
  }

  /* Back of card */
  .card--back { background: var(--card-black); }
  .card-back__texture {
    position: absolute; inset: 0;
    background: linear-gradient(120deg, var(--card-black-soft) 0%, var(--card-black) 45%, #0c0c0c 100%);
  }
  .card-back__brand {
    position: absolute; left: 50%; top: 50%; transform: translate(-50%, -50%);
    display: flex; align-items: center; gap: 12px;
  }
  .brand-dot {
    width: 30px; height: 30px; border-radius: 50%;
    border: 2px solid var(--gold);
  }
  .brand-name {
    color: var(--gold); font-weight: 500; white-space: nowrap;
    letter-spacing: 1px;
  }
  .card-back__brand .brand-name { font-size: 26px; }

  /* Front of card */
  .card--front {
    background: linear-gradient(100deg, var(--card-green-light) 0%, var(--card-green) 35%);
  }
  .card-front__brand {
    position: absolute; left: 48px; top: 70px;
    display: flex; align-items: center; gap: 16px;
  }
  .card-front__brand .brand-dot { width: 52px; height: 52px; border-width: 3px; }
  .card-front__brand .brand-name { font-size: 40px; }

  .card-front__details {
    position: absolute; left: 48px; right: 40px; bottom: 56px;
    display: flex; align-items: flex-end; gap: 20px;
    color: var(--white);
  }
  .person__name { font-size: 22px; line-height: 1.1; white-space: nowrap; }
  .person__first { font-weight: 700; }
  .person__last { font-weight: 300; color: var(--gold); }
  .person__role { font-size: 12px; font-weight: 400; margin-top: 4px; }
  .divider { width: 1px; height: 64px; background: var(--gold); }
  .contact { list-style: none; font-size: 11.5px; line-height: 1.75; }
  .contact li { display: flex; align-items: center; gap: 8px; white-space: nowrap; }
  .contact__icon { width: 12px; height: 12px; flex: none; }
  .contact__bullet {
    width: 10px; height: 10px; border-radius: 50%; background: var(--gold); flex: none;
    margin: 0 1px;
  }
  .contact__spacer { width: 12px; flex: none; }
</style>
</head>
<body>
<main class="stage">
  <section class="card card--back" aria-label="Card back">
    <div class="card-back__texture" role="img" aria-label="Repeating gloss pattern of the brand mark on black"></div>
    <div class="card-back__brand">
      <span class="brand-dot"></span>
      <span class="brand-name">Veloran Cabinets</span>
    </div>
  </section>

  <section class="card card--front" aria-label="Card front">
    <div class="card-front__brand">
      <span class="brand-dot"></span>
      <span class="brand-name">Veloran Cabinets</span>
    </div>

    <div class="card-front__details">
      <div class="person">
        <p class="person__name"><span class="person__first">Mitchell</span> <span class="person__last">Tarrowby</span></p>
        <p class="person__role">Director Craftsman</p>
      </div>
      <span class="divider"></span>
      <ul class="contact">
        <li>
          <svg class="contact__icon" viewBox="0 0 12 12" aria-hidden="true">
            <rect x="0.5" y="2" width="11" height="8" fill="var(--gold)"/>
            <path d="M0.5 2 L6 6.5 L11.5 2" fill="none" stroke="var(--card-green)" stroke-width="1"/>
          </svg>
          info@veloranjoinery-example.com.au
        </li>
        <li><span class="contact__bullet"></span>@veloran.cabinets</li>
        <li><span class="contact__spacer"></span>Western Australia</li>
      </ul>
    </div>
  </section>
</main>
</body>
</html>
```